Building company buisness cards

We are looking for a sharp modern new look for our business cards.
We are a New Zealand based company that specialises in house and land packages.
We have attached a photo of the current logo and would like to see if it can be improved somehow if needed.
We are open to any colours but we have chosen green at this stage.
Feel free to change the font and make the logo smarter looking.
Play with the colours and see what looks best.

We want a card that looks so good know one will want to throw it away!

Target Market(s)

Home buyers

Industry/Entity Type

Building

Contact Information for Business Card

Derek Tolvane
0217394062
dtolvane@quillmarkhomesteads.co.nz
quillmarkhomesteads.co.nz

Font styles to use
Serif
Sans Serif

Colors

Designer to choose colors to be used in the design.

Requirements
Must have
• Logo and company name on one side, details on the other side
Nice to have
• Color codes for the original green are HEX #4a8028, RGB(74,128,40), CMYK(42,0,69,50)
• Round corners, Raised and/or spot UV

```html
<!DOCTYPE html>
<html lang="en">
<head>
<meta charset="utf-8">
<title>Quillmark Homesteads – Business Card</title>
<link rel="stylesheet" href="https://fonts.googleapis.com/css2?family=Open+Sans:wght@400;600;800&display=swap">
<style>
  :root {
    --backdrop: #1d1e20;
    --green: #4a8028;
    --green-deep: #3c7a1c;
    --green-light: #8fe94d;
    --white: #ffffff;
    --ink-grey: #5a5a5a;
    --rule-grey: #c9c9c9;
  }
  * { box-sizing: border-box; margin: 0; padding: 0; }
  html, body {
    width: 1200px; height: 885px; overflow: hidden;
    background: var(--backdrop);
    font-family: "Open Sans", Arial, sans-serif;
  }
  .canvas { position: relative; width: 1200px; height: 885px; }

  .card {
    position: absolute; width: 540px; height: 310px;
    border-radius: 6px; overflow: hidden;
  }

  /* Front side */
  .card-front {
    left: 70px; top: 80px;
    background: linear-gradient(135deg, var(--green-light) 0%, #5fb22e 45%, var(--green-deep) 100%);
  }
  .front-wordmark {
    position: absolute; right: 38px; bottom: 52px;
    color: var(--white); font-weight: 800; line-height: 1;
    text-align: left;
  }
  .front-wordmark .line-top { display: block; font-size: 22px; padding-left: 30px; }
  .front-wordmark .line-bottom { display: block; font-size: 30px; margin-top: 2px; }
  .front-rule {
    position: absolute; right: 110px; bottom: 38px;
    width: 60px; height: 1px; background: rgba(255,255,255,0.35);
  }

  /* Back side */
  .card-back {
    left: 590px; top: 495px;
    background: var(--white);
  }
  .back-wordmark {
    position: absolute; left: 34px; top: 96px;
    color: var(--green); font-weight: 800; line-height: 1;
  }
  .back-wordmark .mark-square {
    display: block; width: 16px; height: 16px; background: var(--green);
    margin: 0 0 10px 70px;
  }
  .back-wordmark .line-top { display: block; font-size: 22px; padding-left: 36px; }
  .back-wordmark .line-bottom { display: block; font-size: 30px; margin-top: 2px; }
  .back-rule {
    position: absolute; left: 110px; top: 196px;
    width: 60px; height: 1px; background: var(--rule-grey);
  }
  .divider {
    position: absolute; left: 262px; top: 60px;
    width: 1px; height: 110px; background: var(--rule-grey);
  }
  .contact {
    position: absolute; left: 282px; top: 70px;
    color: var(--ink-grey);
  }
  .contact-name {
    color: var(--green); font-weight: 600; font-size: 17px;
    letter-spacing: 0.3px; margin-bottom: 8px;
  }
  .contact-row {
    display: flex; align-items: center; gap: 7px;
    font-size: 11.5px; line-height: 1.6;
  }
  .contact-row svg { width: 11px; height: 11px; fill: var(--green); flex: none; }

  .web-band {
    position: absolute; left: 0; right: 0; top: 226px; height: 40px;
    background: var(--green);
    display: flex; align-items: center; padding-left: 110px;
  }
  .web-address {
    color: var(--white); font-size: 13px; letter-spacing: 3px;
  }
</style>
</head>
<body>
<main class="canvas">

  <section class="card card-front" aria-label="Business card front">
    <p class="front-wordmark">
      <span class="line-top">quillmark</span>
      <span class="line-bottom">homesteads.</span>
    </p>
    <span class="front-rule"></span>
  </section>

  <section class="card card-back" aria-label="Business card back">
    <p class="back-wordmark">
      <span class="mark-square"></span>
      <span class="line-top">quillmark</span>
      <span class="line-bottom">homesteads.</span>
    </p>
    <span class="back-rule"></span>

    <span class="divider"></span>

    <div class="contact">
      <p class="contact-name">DEREK TOLVANE</p>
      <p class="contact-row">
        <svg viewBox="0 0 24 24" aria-hidden="true"><path d="M6.6 10.8a15.1 15.1 0 0 0 6.6 6.6l2.2-2.2c.3-.3.7-.4 1-.2 1.1.4 2.3.6 3.6.6.6 0 1 .4 1 1V20c0 .6-.4 1-1 1A17 17 0 0 1 3 4c0-.6.4-1 1-1h3.5c.6 0 1 .4 1 1 0 1.3.2 2.5.6 3.6.1.3 0 .7-.2 1z"/></svg>
        0217394062
      </p>
      <p class="contact-row">
        <svg viewBox="0 0 24 24" aria-hidden="true"><path d="M2 5h20v14H2z M2 5l10 8 10-8" /></svg>
        dtolvane@quillmarkhomesteads.co.nz
      </p>
    </div>

    <div class="web-band">
      <span class="web-address">www.quillmarkhomesteads.co.nz</span>
    </div>
  </section>

</main>
</body>
</html>
```